Postcard design to acquire new clients for my Property Management Company

I'm looking for a postcard design that I can send to prospective clients detailing information about my company and services.
Postcard should be eye catching and contain information from www.bramblecrestpm.com. I've provided a few screen shots for the most important information and my logo.
Target Market(s)
Real Estate
Industry/Entity Type
Real Estate
Font styles to use
Sans Serif
Requirements
Must have
- Must be eye catching!! this will be a direct mail piece - I'd like for the card to be read and not tossed in the trash immediately.
Design que from the logo.
A place to write / print the receipts name and address.
our physical address - 2387 Hollow Pine Road, Lubbock, TX 79852.
Should not have
- the contact information on the business card is not accurate - please use info from website.

```html
<!DOCTYPE html>
<html lang="en">
<head>
<meta charset="utf-8">
<title>Bramblecrest Property Management – Services Postcard</title>
<link href="https://fonts.googleapis.com/css2?family=Montserrat:wght@800&family=Mulish:wght@300;400;700&display=swap" rel="stylesheet">
<style>
  :root {
    --brand-blue: #1a4e8a;
    --band-blue: #164a85;
    --ink-grey: #4a4a4a;
    --bg-light: #c9c9c9;
    --bg-mid: #a9a9a9;
    --panel: rgba(235,235,235,0.35);
    --rule: rgba(26,78,138,0.55);
    --white: #ffffff;
  }
  * { margin: 0; padding: 0; box-sizing: border-box; }
  html, body { width: 1200px; height: 776px; overflow: hidden; background: #e6e6e6; }
  .postcard {
    position: relative; width: 1200px; height: 776px; overflow: hidden;
    background: linear-gradient(160deg, var(--bg-light) 0%, #b8b8b8 45%, var(--bg-mid) 100%);
    font-family: "Mulish", Arial, sans-serif;
  }
  .door-photo {
    position: absolute; left: 760px; top: 0; width: 440px; height: 776px;
    background: linear-gradient(90deg, rgba(170,170,170,0) 0%, #8e8e8e 30%, #3a3a3a 58%, #9a9a9a 66%, #2a2a2a 78%, #d8d8d8 92%, #f2f2f2 100%);
  }
  .brand {
    position: absolute; left: 84px; top: 76px;
    color: var(--brand-blue); font-weight: 700; text-transform: uppercase;
  }
  .brand-name { display: block; font-size: 29px; letter-spacing: 5px; line-height: 30px; }
  .brand-sub { display: block; font-size: 14px; letter-spacing: 3.6px; line-height: 18px; margin-top: 2px; }
  .return-address {
    position: absolute; left: 84px; top: 134px;
    font-size: 12px; font-weight: 400; line-height: 16px; color: var(--brand-blue);
  }
  .recipient {
    position: absolute; left: 450px; top: 78px; width: 280px;
    color: var(--brand-blue);
  }
  .recipient-label {
    font-size: 11px; font-weight: 700; letter-spacing: 2px; text-transform: uppercase;
  }
  .recipient-line { height: 24px; border-bottom: 1px solid var(--rule); }
  .headline {
    position: absolute; left: 84px; top: 234px;
    font-family: "Montserrat", Arial, sans-serif; font-weight: 800;
    font-size: 48px; letter-spacing: 0.5px; color: var(--brand-blue); line-height: 56px;
  }
  .tagline {
    position: absolute; left: 84px; top: 289px;
    font-weight: 300; font-size: 27.5px; color: var(--brand-blue); white-space: nowrap;
  }
  .services-panel {
    position: absolute; left: 0; top: 343px; width: 995px; height: 334px;
    background: var(--panel);
  }
  .service { position: absolute; width: 160px; text-align: center; }
  .service svg { display: block; margin: 0 auto; height: 42px; width: 50px; fill: var(--brand-blue); }
  .service-title {
    margin-top: 6px; font-weight: 700; font-size: 15px; color: var(--brand-blue); white-space: nowrap;
  }
  .service-text {
    margin: 5px auto 0; width: 152px; font-weight: 300; font-size: 10px; line-height: 13.2px; color: var(--ink-grey);
  }
  .contact-band {
    position: absolute; left: 0; top: 683px; width: 1000px; height: 64px;
    background: var(--band-blue); color: var(--white);
    display: flex; align-items: center; padding-left: 84px; gap: 14px;
  }
  .contact-label { font-weight: 300; font-size: 26px; letter-spacing: 0.5px; }
  .contact-details { font-weight: 700; font-size: 21px; }
</style>
</head>
<body>
<div class="postcard">
  <div class="door-photo" role="img" aria-label="Black and white photo of a door handle with a ring of keys hanging from the lock"></div>

  <div class="brand">
    <span class="brand-name">Bramblecrest</span>
    <span class="brand-sub">Property Management</span>
  </div>
  <p class="return-address">2387 Hollow Pine Road<br>Lubbock, TX 79852</p>

  <div class="recipient">
    <div class="recipient-label">Recipient</div>
    <div class="recipient-line"></div>
    <div class="recipient-line"></div>
    <div class="recipient-line"></div>
  </div>

  <h1 class="headline">DISCOVER OUR SERVICES</h1>
  <p class="tagline">We offer full-service property management solutions</p>

  <div class="services-panel"></div>

  <div class="service" style="left:81px;top:358px">
    <svg viewBox="0 0 50 42"><path d="M25 2 2 22h6v18h13V28h8v12h13V22h6L38 11V4h-6v2z"/></svg>
    <div class="service-title">Property Marketing</div>
    <p class="service-text">Tired of waiting for weeks on end, hoping to find a new tenant? Let us take over your marketing for you and we'll find a qualified renter quickly.</p>
  </div>
  <div class="service" style="left:260px;top:358px">
    <svg viewBox="0 0 50 42"><circle cx="17" cy="10" r="8"/><circle cx="36" cy="12" r="7"/><path d="M2 40c0-12 6-18 15-18s15 6 15 18zM30 40c0-7-1-12-4-15 3-2 6-3 10-3 8 0 12 6 12 18z"/></svg>
    <div class="service-title">Tenant Screening</div>
    <p class="service-text">We don't just find someone to rent your home—we find the best renters. We screen all applications using fair housing guidelines to protect you.</p>
  </div>
  <div class="service" style="left:437px;top:358px">
    <svg viewBox="0 0 50 42"><text x="25" y="38" text-anchor="middle" font-family="Mulish, Arial, sans-serif" font-weight="700" font-size="44" fill="#1a4e8a">$</text></svg>
    <div class="service-title">Rent Collection</div>
    <p class="service-text">Stop guessing when you'll receive your rental earnings every month and say hello to consistent payments. We keep your tenants current.</p>
  </div>
  <div class="service" style="left:614px;top:358px">
    <svg viewBox="0 0 50 42"><path d="M28 6c6-4 14-3 18 2l-5 4-5-2-3 4 3 3-4 4-3-3L10 40 5 35 27 14l-3-3z"/></svg>
    <div class="service-title">Maintenance</div>
    <p class="service-text">Still scrambling to respond to repair requests every time you receive a tenant call? Let us coordinate repair work on your behalf!</p>
  </div>

  <div class="service" style="left:81px;top:516px">
    <svg viewBox="0 0 50 42"><circle cx="21" cy="17" r="12" fill="none" stroke="#1a4e8a" stroke-width="5"/><path d="M29 25l4-4 12 12-4 4z"/></svg>
    <div class="service-title">Property Inspections</div>
    <p class="service-text">Inspections form an important part of our proactive property management approach. We visit every home in our portfolio regularly.</p>
  </div>
  <div class="service" style="left:260px;top:516px">
    <svg viewBox="0 0 50 42"><path d="M4 2h4v34h40v4H4z"/><rect x="13" y="22" width="4" height="12"/><rect x="21" y="16" width="4" height="18"/><rect x="29" y="19" width="4" height="15"/><rect x="37" y="10" width="4" height="24"/></svg>
    <div class="service-title">Financial Reporting</div>
    <p class="service-text">Keep a handle on your real estate performance. We generate monthly statements so you can review income &amp; expenses at a moment's notice.</p>
  </div>
  <div class="service" style="left:437px;top:516px">
    <svg viewBox="0 0 50 42"><path d="M25 2 9 8v12c0 10 7 17 16 20 9-3 16-10 16-20V8zm0 5v28c-6-3-11-8-11-15v-9z"/></svg>
    <div class="service-title">Evictions</div>
    <p class="service-text">When things go wrong inside your rental home, rest easy with the experts on your side. We will handle evictions for you &amp; find new renters when its over.</p>
  </div>
  <div class="service" style="left:614px;top:516px">
    <svg viewBox="0 0 50 42"><path d="M23 4h4v30h10v4H13v-4h10z"/><path d="M6 10h38v3H6z"/><path d="M10 13 3 27h14zM10 17l4 8H6z"/><path d="M40 13l-7 14h14zM40 17l4 8h-8z"/><path d="M2 27h16c0 4-4 6-8 6s-8-2-8-6zM32 27h16c0 4-4 6-8 6s-8-2-8-6z"/></svg>
    <div class="service-title">Legal Guidance</div>
    <p class="service-text">Don't accidentally violate one of the many ordinances and housing laws governing your relationship with your tenants. Let us keep you compliant.</p>
  </div>

  <div class="contact-band">
    <span class="contact-label">Contact Our Team</span>
    <span class="contact-details">(806) 555-0142 | info@bramblecrestpm.com</span>
  </div>
</div>
</body>
</html>
```